Business Card for Coastal Tundrabridge Advisory

We need a business card for Coastal Tundrabridge Advisory. The company website address is provided below. The company logo is attached. We provide specialized permafrost services to the mining, transportation, and oil & gas industries. The card should be prepared for:
Matthias Korhonen, PhD.
Coastal Tundrabridge Advisory
PO Box 418259
Quillwater, Alaska 99642
Direct: +1-907-555-0143
Email: mkorhonen@tundrabridgeadvisory.example
Website: www.coastaltundrabridgeadvisory.example

```html
<!DOCTYPE html>
<html lang="en">
<head>
<meta charset="utf-8">
<title>Coastal Tundrabridge Advisory – Business Card</title>
<link href="https://fonts.googleapis.com/css2?family=Montserrat:wght@400;500;600;700&display=swap" rel="stylesheet">
<style>
  :root {
    --bg: #e9e8ea;
    --paper: #ffffff;
    --navy: #131a24;
    --ink: #1b1f26;
    --emboss: #27344a;
  }
  * { margin: 0; padding: 0; box-sizing: border-box; }
  html, body {
    width: 1200px; height: 1108px; overflow: hidden;
    background: var(--bg);
    font-family: "Montserrat", sans-serif;
    color: var(--ink);
  }
  .canvas { position: relative; width: 1200px; height: 1108px; }
  .card { position: absolute; width: 740px; height: 444px; overflow: hidden; }
  .card-front { left: 241px; top: 68px; background: var(--paper); }
  .card-back { left: 248px; top: 590px; height: 441px; background: var(--navy);
    display: flex; align-items: center; justify-content: center; }

  .wave { position: absolute; left: 0; top: 0; width: 740px; height: 444px; }

  .person { position: absolute; left: 45px; top: 76px; }
  .person-name { font-size: 22px; font-weight: 700; letter-spacing: 0.2px; }
  .person-title { font-size: 15.5px; font-weight: 500; margin-top: 2px; }

  .brand-name {
    position: absolute; right: 34px; top: 80px; width: 290px;
    text-align: center;
    font-size: 21px; font-weight: 600; line-height: 1.25;
    letter-spacing: 1.5px; text-transform: uppercase; color: var(--navy);
  }

  .address { position: absolute; left: 52px; top: 186px; font-size: 16px; line-height: 21px; }

  .contacts { position: absolute; left: 50px; top: 257px; list-style: none; }
  .contacts li { display: flex; align-items: center; height: 31px; font-size: 15.5px; }
  .contacts svg { width: 16px; height: 16px; margin-right: 12px; fill: var(--ink); flex: none; }

  .back-brand {
    font-size: 40px; font-weight: 600; letter-spacing: 4px;
    text-transform: uppercase; color: var(--emboss);
    text-align: center; line-height: 1.2;
  }
</style>
</head>
<body>
<div class="canvas">

  <section class="card card-front">
    <svg class="wave" viewBox="0 0 740 444" aria-hidden="true">
      <path d="M0,320 C60,382 200,386 330,372 C480,356 600,338 740,344 L740,444 L0,444 Z" fill="var(--navy)"/>
      <path d="M0,352 C80,410 220,415 360,398 C500,382 620,352 740,350" fill="none" stroke="#fff" stroke-width="3"/>
    </svg>

    <div class="person">
      <div class="person-name">Matthias Korhonen, PhD.</div>
      <div class="person-title">Managing Director</div>
    </div>

    <div class="brand-name">Coastal Tundrabridge Advisory</div>

    <div class="address">
      <div>PO Box 418259</div>
      <div>Quillwater, Alaska 99642</div>
    </div>

    <ul class="contacts">
      <li>
        <svg viewBox="0 0 24 24"><path d="M6.6 10.8a15.1 15.1 0 0 0 6.6 6.6l2.2-2.2a1 1 0 0 1 1-.25 11.4 11.4 0 0 0 3.6.57 1 1 0 0 1 1 1V20a1 1 0 0 1-1 1A17 17 0 0 1 3 4a1 1 0 0 1 1-1h3.5a1 1 0 0 1 1 1c0 1.25.2 2.45.57 3.57a1 1 0 0 1-.25 1z"/></svg>
        +1-907-555-0143
      </li>
      <li>
        <svg viewBox="0 0 24 24"><path d="M2 5h20v14H2z M2 5l10 7 10-7" /><path d="M3 6.5l9 6.3 9-6.3" fill="#fff"/></svg>
        mkorhonen@tundrabridgeadvisory.example
      </li>
      <li>
        <svg viewBox="0 0 24 24"><circle cx="12" cy="12" r="10"/><path d="M7 6c2 1 3 3 2 5s-3 2-3 4M15 4c-1 2 0 3 2 4s2 3 1 5M12 20c0-2 1-3 3-4" stroke="#fff" stroke-width="1.6" fill="none"/></svg>
        www.coastaltundrabridgeadvisory.example
      </li>
    </ul>
  </section>

  <section class="card card-back">
    <div class="back-brand">Coastal Tundrabridge<br>Advisory</div>
  </section>

</div>
</body>
</html>
```